Velmora Consulting Business

** Please add the content information from my old business card
1. I would like to see a two sided business card with both options with the 1st Option--Tallow Spire-new WHITE BACKGROUND LOGO
2 nd Option-Tallow Spire - new BLACK- Background Logo
3rd -Option a business card with my Photo on the card
Please add the new word to the card information:
EXECUTION
AS THE OWNER'S REP
WE AIM TO ACHIEVE YOUR
INFRASTRUCTURE VISION with
OUR SPECIALIZATION & EXECUTION in:

FUNDING Planning
BUSINESS Planning
INFRASTRUCTURE Planning
PROJECT Management
Since 2012
_____________________________________________________________________
I want to get spot uv raised printing. I was liking a a nice rich white linen paper stock with black writing & NOT A COLORED CARD other than a variety of white or black cards concept

```html
<!DOCTYPE html>
<html lang="en">
<head>
<meta charset="utf-8">
<title>Velmora Consulting – Business Card</title>
<link rel="stylesheet" href="https://fonts.googleapis.com/css2?family=Montserrat:wght@400;500;700&family=Libre+Baskerville:wght@400;700&display=swap">
<style>
  :root {
    --stage: #2b2b2e;
    --card-black: #161617;
    --card-white: #ffffff;
    --accent-red: #e3122f;
    --ink-black: #141414;
    --ink-light: #e9e9e9;
    --ink-muted: #3a3a3c;
    --ink-emboss: #3d3d40;
  }
  * { box-sizing: border-box; margin: 0; padding: 0; }
  html, body {
    width: 1200px; height: 900px; overflow: hidden;
    background: var(--stage);
  }
  .stage {
    width: 1200px; height: 900px;
    display: flex; flex-direction: column;
    align-items: center; justify-content: center; gap: 48px;
  }
  .card {
    position: relative;
    width: 660px; height: 377px;
    border-radius: 22px;
    border-bottom: 4px solid var(--accent-red);
    display: flex; align-items: center;
    padding: 0 40px 0 50px;
    box-shadow: 0 14px 30px rgba(0,0,0,.45);
  }
  .card--back { background: var(--card-black); color: var(--ink-light); }
  .card--front { background: var(--card-white); color: var(--ink-black); }

  .brand {
    width: 230px; flex: none;
    display: flex; align-items: center; gap: 12px;
  }
  .brand__mark {
    width: 14px; height: 14px; flex: none;
    background: var(--accent-red);
  }
  .brand__name {
    font-family: "Montserrat", sans-serif;
    font-weight: 700; font-size: 32px; line-height: 1.05;
    letter-spacing: -0.5px;
  }
  .card--back .brand__name { color: var(--ink-emboss); }
  .card--front .brand__name { color: var(--ink-black); }

  .divider {
    width: 2px; flex: none; align-self: stretch;
    margin: 66px 28px;
    background: var(--accent-red);
  }

  .pitch { flex: 1; }
  .pitch__lead {
    font-family: "Libre Baskerville", serif;
    font-size: 12.5px; line-height: 1.4;
    color: var(--accent-red); text-transform: uppercase;
    margin-bottom: 20px;
  }
  .pitch__lead strong { font-family: "Montserrat", sans-serif; font-weight: 700; }
  .pitch__lead .lower { text-transform: none; }
  .services { list-style: none; }
  .services li {
    font-family: "Montserrat", sans-serif;
    font-size: 15px; line-height: 1.75;
    display: flex; align-items: center; gap: 12px;
  }
  .services li::before {
    content: ""; width: 8px; height: 8px;
    background: var(--accent-red); transform: rotate(45deg);
  }
  .since {
    position: absolute; right: 40px; bottom: 30px;
    font-family: "Montserrat", sans-serif; font-size: 11px;
    color: var(--ink-muted);
  }

  .contact { flex: 1; min-width: 0; font-family: "Montserrat", sans-serif; }
  .contact__name {
    color: var(--accent-red); font-weight: 700; font-size: 20px;
    line-height: 1.2; white-space: nowrap;
  }
  .contact__role { font-size: 13px; font-weight: 500; margin-top: 4px; white-space: nowrap; }
  .contact__region { font-size: 13px; margin-top: 6px; margin-bottom: 14px; white-space: nowrap; }
  .contact__line {
    display: flex; align-items: center; gap: 10px;
    font-size: 14px; line-height: 1.7;
  }
  .contact__icon { width: 14px; height: 14px; flex: none; }
</style>
</head>
<body>
<main class="stage">

  <section class="card card--back" aria-label="Card back">
    <div class="brand">
      <span class="brand__mark"></span>
      <span class="brand__name">Velmora Consulting</span>
    </div>
    <span class="divider"></span>
    <div class="pitch">
      <p class="pitch__lead">As the <strong>Owner's Rep</strong><br>We aim to achieve your<br>infrastructure vision <span class="lower">with</span><br>our specialization &amp; execution <span class="lower">in:</span></p>
      <ul class="services">
        <li>FUNDING Planning</li>
        <li>BUSINESS Planning</li>
        <li>INFRASTRUCTURE Planning</li>
        <li>PROJECT Management</li>
      </ul>
    </div>
    <span class="since">Since 2012</span>
  </section>

  <section class="card card--front" aria-label="Card front">
    <div class="brand">
      <span class="brand__mark"></span>
      <span class="brand__name">Velmora Consulting</span>
    </div>
    <span class="divider"></span>
    <div class="contact">
      <p class="contact__name">Marissa Doyle-Hartwell</p>
      <p class="contact__role">CEO / LEAD PROJECT MANAGER</p>
      <p class="contact__region">Kestrel Bay · Marlowe Falls</p>
      <p class="contact__line">
        <svg class="contact__icon" viewBox="0 0 16 16" aria-hidden="true"><path fill="#e3122f" d="M3.6 1.5 6 4 4.8 5.6a9 9 0 0 0 5.6 5.6L12 10l2.5 2.4-1.6 2.1C7 14.2 1.8 9 1.5 3.1z"/></svg>
        555.014.2290
      </p>
      <p class="contact__line">
        <svg class="contact__icon" viewBox="0 0 16 16" aria-hidden="true"><rect x="1" y="3" width="14" height="10" rx="1" fill="#e3122f"/><path d="M1.5 4 8 9l6.5-5" fill="none" stroke="#fff" stroke-width="1.3"/></svg>
        marissa@velmora.ca
      </p>
      <p class="contact__line">
        <svg class="contact__icon" viewBox="0 0 16 16" aria-hidden="true"><circle cx="8" cy="8" r="6.5" fill="none" stroke="#e3122f" stroke-width="1.6"/><ellipse cx="8" cy="8" rx="2.8" ry="6.5" fill="none" stroke="#e3122f" stroke-width="1.2"/><path d="M1.5 8h13" stroke="#e3122f" stroke-width="1.2"/></svg>
        www.velmora.ca
      </p>
    </div>
  </section>

</main>
</body>
</html>
```